Bookcover: Ways to Turn Into a Bold Pathfinder

I am publishing a super-low-cost innovation book for €4,99 on Quillmere Open Press to help everyone become a great innovator: young ambitious people without college education nor a big budget. Do you want to help me?

Brief:
Design a book cover 1600 x 2560 pixels for QOP.
Main title: Ways to Turn Into a Bold Pathfinder
Sub title: mindset - insights - skills & tools
Author: Joost ter Brakel
Design: captive, and appealing to everyone
Target Group: young ambitious people without college education

For quillmere please format the height/width ratio of 1.6:1

```html
<!DOCTYPE html>
<html lang="en">
<head>
<meta charset="utf-8">
<title>Ways to Turn Into a Bold Pathfinder — Book Cover</title>
<link href="https://fonts.googleapis.com/css2?family=Montserrat:wght@800;900&display=swap" rel="stylesheet">
<style>
  :root {
    --night: #1f2358;
    --night-deep: #14174a;
    --ember: #e06000;
    --sun: #ff7d00;
    --sun-light: #ff9a10;
    --paper: #ffffff;
    --ridge-gold: #c98a4a;
  }
  html, body {
    margin: 0;
    padding: 0;
    overflow: hidden;
    background: var(--night);
  }
  .cover {
    position: relative;
    width: 750px;
    height: 1200px;
    overflow: hidden;
    background: var(--night);
    font-family: "Montserrat", sans-serif;
    font-weight: 900;
    color: var(--paper);
  }
  .sun {
    position: absolute;
    left: 60px;
    top: -62px;
    width: 158px;
    height: 158px;
    border-radius: 50%;
    background: radial-gradient(circle at 70% 25%, var(--sun-light), var(--sun) 55%, #f06a00);
  }
  .kicker {
    position: absolute;
    top: 146px;
    left: 0;
    width: 750px;
    text-align: center;
    font-size: 38px;
    letter-spacing: 14px;
    line-height: 1;
    text-indent: 14px;
    white-space: nowrap;
  }
  .title-frame {
    position: absolute;
    left: 48px;
    top: 220px;
    width: 649px;
    height: 505px;
    border: 1px solid var(--paper);
  }
  .title {
    position: absolute;
    left: 72px;
    width: 606px;
    margin: 0;
    font-size: 142px;
    line-height: 1;
    color: var(--ember);
    display: flex;
    justify-content: space-between;
  }
  .title--one { top: 254px; }
  .title--two { top: 404px; }
  .title--three { top: 556px; }
  .subtitle {
    position: absolute;
    left: 0;
    width: 750px;
    text-align: center;
    font-size: 42px;
    letter-spacing: 9px;
    text-indent: 9px;
    line-height: 1;
    white-space: nowrap;
  }
  .subtitle--one { top: 758px; }
  .subtitle--two { top: 812px; }
  .ridges {
    position: absolute;
    left: 0;
    top: 880px;
    width: 750px;
    height: 320px;
    background: linear-gradient(180deg, rgba(201,138,74,0.55) 0%, rgba(224,96,0,0.45) 35%, rgba(31,35,88,0.9) 100%), var(--night);
  }
  .author-band {
    position: absolute;
    left: 0;
    top: 1110px;
    width: 750px;
    height: 90px;
    background: rgba(20, 23, 74, 0.75);
  }
  .author {
    position: absolute;
    top: 1128px;
    left: 0;
    width: 750px;
    text-align: center;
    font-size: 44px;
    letter-spacing: 11px;
    text-indent: 11px;
    line-height: 1;
    white-space: nowrap;
  }
</style>
</head>
<body>
  <main class="cover">
    <div class="sun"></div>
    <p class="kicker" style="margin:0">WAYS TO TURN INTO A</p>
    <div class="title-frame"></div>
    <h1 class="title title--one"><span>B</span><span>O</span><span>L</span><span>D</span></h1>
    <h1 class="title title--two"><span>P</span><span>A</span><span>T</span><span>H</span><span>-</span></h1>
    <h1 class="title title--three"><span>F</span><span>I</span><span>N</span><span>D</span><span>E</span><span>R</span></h1>
    <p class="subtitle subtitle--one" style="margin:0">MINDSET-INSIGHTS</p>
    <p class="subtitle subtitle--two" style="margin:0">SKILS &amp; TOOLS</p>
    <div class="ridges" role="img" aria-label="Line-art illustration of layered gold and orange mountain peaks against a night sky"></div>
    <div class="author-band"></div>
    <p class="author" style="margin:0">JOOST TER BRAKEL</p>
  </main>
</body>
</html>
```